Realty Group Needs Classy, Contemporary Letterhead Design

We need a letterhead design for a new realty company located in NY, USA. We buy investment properties to rehabilitate and or keep in our rental portfolio.

```html
<!DOCTYPE html>
<html lang="en">
<head>
<meta charset="utf-8">
<title>Meridian Realty Group – Letterhead</title>
<link rel="stylesheet" href="https://fonts.googleapis.com/css2?family=Open+Sans:wght@400;700&family=Lato:wght@400&display=swap">
<style>
  :root {
    --brand-purple: #4b2a86;
    --brand-purple-soft: #8a72b8;
    --ink: #3a3a3a;
    --ink-dark: #1e1e1e;
    --paper: #ffffff;
  }
  * { margin: 0; padding: 0; box-sizing: border-box; }
  html, body { width: 1040px; height: 1200px; overflow: hidden; background: var(--paper); }
  .letterhead {
    position: relative; width: 1040px; height: 1200px; overflow: hidden;
    background: var(--paper); font-family: "Open Sans", sans-serif; color: var(--ink);
  }
  .brand {
    position: absolute; top: 44px; right: 110px;
    display: flex; align-items: center; gap: 12px;
  }
  .brand-dot { width: 20px; height: 20px; border-radius: 50%; background: var(--brand-purple); }
  .brand-name {
    font-family: "Open Sans", sans-serif; font-weight: 700; font-size: 36px;
    color: var(--brand-purple); letter-spacing: 0.5px; line-height: 1.1; text-align: center;
  }
  .brand-name small { display: block; font-size: 14px; letter-spacing: 1px; }
  .letter-body { position: absolute; left: 98px; width: 840px; font-size: 15.5px; line-height: 20px; }
  .issue-date { top: 236px; }
  .recipient { top: 272px; line-height: 18px; }
  .salutation { top: 376px; }
  .content { top: 430px; line-height: 27px; text-align: justify; hyphens: auto; }
  .content p + p { margin-top: 27px; }
  .closing { top: 834px; }
  .signature {
    position: absolute; left: 98px; top: 868px; width: 220px; height: 26px;
    background: linear-gradient(90deg, #e4e0ec, #f4f2f8);
  }
  .signer-name { top: 910px; font-size: 19.5px; line-height: 24px; color: var(--ink-dark); }
  .signer-title { top: 940px; }
  .footer-band {
    position: absolute; left: 0; right: 0; top: 1086px; bottom: 0; background: var(--brand-purple);
  }
  .footer-art {
    position: absolute; left: 0; top: 978px; width: 400px; height: 222px;
    background: linear-gradient(160deg, #ffffff 0%, var(--brand-purple-soft) 45%, var(--brand-purple) 80%);
  }
  .footer-address {
    position: absolute; right: 108px; top: 1050px;
    font-family: "Lato", sans-serif; font-size: 18px; color: var(--ink-dark);
  }
  .contact-list {
    position: absolute; right: 108px; top: 1110px; list-style: none;
    font-family: "Lato", sans-serif; font-size: 18px; color: var(--paper);
    text-align: right; line-height: 22px;
  }
  .icon { position: absolute; right: 86px; width: 17px; height: 17px; }
  .icon-pin { top: 1053px; }
</style>
</head>
<body>
<main class="letterhead">
  <header class="brand">
    <span class="brand-dot"></span>
    <div class="brand-name">MERIDIAN<small>Realty Group, LLC</small></div>
  </header>

  <p class="letter-body issue-date">Issuing Date: May 5, 2018</p>
  <address class="letter-body recipient" style="font-style:normal">
    Name Of Employee Mr. XYZABC<br>Address of Employee<br>Address Line 2 etc..
  </address>
  <p class="letter-body salutation">Dear Mr.XYZABC</p>

  <section class="letter-body content">
    <p>Lorem Ipsum has been the industry's standard dummy text ever since the 1500s, when an unknown printer took a galley of type and scrambled it to make a type specimen book. It has survived not only five centuries, but also the leap into electronic typesetting, remaining essentially unchanged. It was popularised in the 1960s with the release of Letraset sheets containing Lorem Ipsum passages, and more recently with desktop publishing software like Aldus PageMaker including versions of Lorem Ipsum.</p>
    <p>Lorem Ipsum is simply dummy text of the printing and typesetting industry. Lorem Ipsum has been the industry's standard dummy text ever since the 1500s, when an unknown printer took a galley of type and scrambled it to make a type specimen book.</p>
    <p>It has survived not only five centuries, but also the leap into electronic typesetting, remaining essentially unchanged. It was popularised in the 1960s with the release of Letraset sheets containing Lorem IpsumIpsum passages.</p>
  </section>

  <p class="letter-body closing">Yours Sincerely</p>
  <div class="signature" role="img" aria-label="Handwritten signature of Daniel Ashford"></div>
  <p class="letter-body signer-name">Daniel Ashford</p>
  <p class="letter-body signer-title">Managing Director</p>

  <div class="footer-band"></div>
  <div class="footer-art" role="img" aria-label="Purple silhouette illustration of an archer drawing a bow"></div>

  <p class="footer-address">421, Address line here Country Name, 45452</p>
  <svg class="icon icon-pin" viewBox="0 0 16 20" aria-hidden="true">
    <path d="M8 0C3.6 0 0 3.4 0 7.6 0 13 8 20 8 20s8-7 8-12.4C16 3.4 12.4 0 8 0z" fill="var(--brand-purple)"/>
    <circle cx="8" cy="7.5" r="3" fill="#fff"/>
  </svg>

  <ul class="contact-list">
    <li>044-123 456 789</li>
    <li>info@webname.com</li>
    <li>www.websitename.com</li>
  </ul>
  <svg class="icon" style="top:1113px" viewBox="0 0 16 16" aria-hidden="true">
    <path d="M1 6c0-2 3-3 7-3s7 1 7 3v1h-3V5.5H4V7H1z M3 8h10l1 6H2z" fill="#fff"/>
  </svg>
  <svg class="icon" style="top:1135px" viewBox="0 0 16 16" aria-hidden="true">
    <rect x="1" y="3" width="14" height="10" fill="#fff"/>
    <path d="M1.5 3.5 8 9l6.5-5.5" fill="none" stroke="var(--brand-purple)" stroke-width="1.4"/>
  </svg>
  <svg class="icon" style="top:1157px" viewBox="0 0 16 16" aria-hidden="true">
    <circle cx="8" cy="8" r="7" fill="#fff"/>
    <path d="M5 4c2 1 1 3 3 3s1 3 3 3M9 13c0-2 2-2 3-3" fill="none" stroke="var(--brand-purple)" stroke-width="1.4"/>
  </svg>
</main>
</body>
</html>
```